Brand new redesign of Brightpath finance website

I need a new website design that i can advertise a great low interest rate on the front page and capture input application details that will send through to my email address.

some car finance companies will be similar to this would be listed below

tallowcredit.example.com.au
mirabelfinance.example.com.au
finance725.example.com.au
quenbyfinance.example.com.au
finance91.example.com.au

Reason: I have changed the project to a committed project. all the webpages should have the same format just different content and i want to be able to edit the front page easily to update my interest rates.

Target Market(s)

Australian Finance market targeting a younger demographic

Industry/Entity Type

Finance

Coding

Coded - Design and coding required

Number of Pages Required

5+ page

Font styles to use
Serif
Sans Serif

Colors
0255a3
ffffff
cedeed

Requirements
Must have
• application capture form
• apply now buttons
• Headline rate front page

```html
<!DOCTYPE html>
<html lang="en">
<head>
<meta charset="utf-8">
<title>Brightpath Finance</title>
<link rel="stylesheet" href="https://fonts.googleapis.com/css2?family=Open+Sans:wght@300;400;600;700&family=Oswald:wght@400;500&display=swap">
<style>
:root{
  --brand:#0255a3;
  --brand-dark:#1d3f8a;
  --sky:#0aa3e6;
  --ink:#333333;
  --nav-bg:#eeeeee;
  --white:#ffffff;
  --pale:#cedeed;
  --footer:#262223;
  --footer-deep:#1c191a;
  --muted:#8a8a8a;
}
*{box-sizing:border-box;margin:0;padding:0}
html,body{width:900px;height:1200px;overflow:hidden}
body{font-family:"Open Sans",Arial,sans-serif;color:var(--ink);background:var(--white);position:relative}
.abs{position:absolute}

/* header */
.brand{left:121px;top:12px;display:flex;align-items:center;gap:8px}
.brand-mark{width:30px;height:30px;border-radius:50%;background:var(--brand)}
.brand-name{font-weight:700;font-size:18px;color:var(--brand);letter-spacing:.5px;text-transform:uppercase;line-height:1}
.call{left:552px;top:16px;font-size:12px;color:var(--brand);font-weight:600}
.call strong{color:var(--ink);font-size:15px;font-weight:600;margin-left:3px}
.social-top{left:702px;top:15px;display:flex;gap:8px}
.social-top span{width:20px;height:20px;background:#8f8f8f;display:block}

/* nav */
.nav{left:0;top:54px;width:900px;height:28px;background:var(--nav-bg)}
.nav ul{list-style:none;position:absolute;left:121px;top:0;width:658px;height:28px;display:flex}
.nav li{height:28px;display:flex;align-items:center;justify-content:center;font-size:9.5px;color:#222;border-right:1px solid #d6d6d6;gap:6px}
.nav li:last-child{border:0;background:var(--brand);color:var(--white)}

/* hero */
.hero{left:0;top:82px;width:900px;height:338px;background:linear-gradient(100deg,#1d5a96 0%,#2a78b4 45%,#4ea3d2 100%)}
.hero-h1{left:124px;top:148px;color:var(--white);font-size:29px;font-weight:600;line-height:1.1}
.hero-h2{left:124px;top:184px;color:var(--white);font-size:23px;font-weight:300}
.hero-h3{left:124px;top:215px;color:var(--white);font-size:22px;font-weight:600}
.rate-label{top:270px;color:var(--white);font-family:"Oswald",sans-serif;font-size:14px}
.rate-box{top:292px;width:137px;height:61px;background:var(--white);display:flex;align-items:center;justify-content:center;gap:4px;color:#2168a8;font-family:"Oswald",sans-serif}
.rate-box .num{font-size:46px;font-weight:500;line-height:1}
.rate-box .unit{font-size:15px;line-height:.9;font-weight:500}

.quote{left:538px;top:135px;width:240px;height:234px;background:rgba(20,75,130,.55)}
.quote h3{position:absolute;left:0;width:100%;top:14px;text-align:center;color:var(--white);font-weight:400;font-size:20px}
.field{position:absolute;left:17px;width:206px;height:26px;background:var(--white);font-size:8px;color:#666;padding-left:9px;display:flex;align-items:center}
.field svg{position:absolute;right:9px;top:11px}
.quote .btn{position:absolute;left:17px;top:187px;width:206px;height:29px;background:var(--sky);color:var(--white);font-size:10px;display:flex;align-items:center;justify-content:center}

/* services */
.services-title{left:0;width:900px;top:458px;text-align:center;font-size:23px;font-weight:600;color:#2b2b2b}
.tile{width:215px;height:140px;display:flex;align-items:flex-end;justify-content:center;padding-bottom:12px;color:var(--white);font-size:11.5px;font-weight:600}
.t-vehicle{background:linear-gradient(160deg,#c8a7ad,#7b5a5e 60%,#8b2337)}
.t-boat{background:linear-gradient(180deg,#7fb0d8,#b8b09a 45%,#2f8aa3)}
.t-home{background:linear-gradient(180deg,#a9c9e4,#e8e8e2 40%,#4b6b2f)}
.t-personal{background:linear-gradient(120deg,#9ab4c4,#6c8ea8 55%,#43627e)}
.t-business{background:linear-gradient(160deg,#b8d2ea,#3f6ea3 55%,#1d3a66)}
.t-equipment{background:linear-gradient(180deg,#5d87b8,#c9a93a 55%,#4a3e2e)}

/* cta */
.cta{left:0;top:843px;width:900px;height:199px;background:linear-gradient(100deg,#3aa3c4 0%,#3b6fa6 50%,#5b4c9c 100%)}
.cta h2{position:absolute;left:0;width:100%;top:40px;text-align:center;color:var(--white);font-weight:300;font-size:27px}
.cta h2 b{font-weight:700}
.cta p{position:absolute;left:0;width:100%;top:74px;text-align:center;color:var(--white);font-size:10.5px}
.cta .outline{position:absolute;left:385px;top:122px;width:130px;height:33px;border:1px solid var(--white);color:var(--white);font-size:10px;display:flex;align-items:center;justify-content:center}

/* footer */
.footer{left:0;top:1042px;width:900px;height:124px;background:var(--footer)}
.footer .brand{left:121px;top:38px}
.footer .brand-name{color:#3d6fc0}
.foot-rule{left:289px;top:38px;width:1px;height:34px;background:#3d6fc0}
.foot-about{left:305px;top:36px;width:170px;color:#ddd;font-size:8.5px;line-height:1.55}
.foot-head{top:28px;color:#eee;font-size:11px}
.foot-text{color:#eee;font-size:8.5px;line-height:1.6}
.contact-row{display:flex;align-items:center;gap:9px;font-size:8.5px;color:#eee;height:17px}
.bottom{left:0;top:1166px;width:900px;height:34px;background:var(--footer-deep)}
.social-foot{left:123px;top:7px;display:flex;gap:11px}
.social-foot span{width:20px;height:20px;border-radius:50%;background:#3a3637;display:block}
.copy{right:125px;top:11px;color:#ccc;font-size:8.5px}
</style>
</head>
<body>

<header>
  <div class="abs brand"><span class="brand-mark"></span><span class="brand-name">Brightpath Finance</span></div>
  <div class="abs call">Call us: <strong>1300-555-014</strong></div>
  <div class="abs social-top"><span></span><span></span><span></span></div>
</header>

<nav class="abs nav">
  <ul>
    <li style="width:116px">HOME</li>
    <li style="width:93px">ABOUT</li>
    <li style="width:101px">LOAN
      <svg width="8" height="5" viewBox="0 0 8 5"><path d="M1 1l3 3 3-3" fill="none" stroke="#222" stroke-width="1"/></svg></li>
    <li style="width:149px">LOAN CALCULATOR</li>
    <li style="width:106px">CONTACT</li>
    <li style="width:93px">APPLY NOW</li>
  </ul>
</nav>

<section class="abs hero" role="img" aria-label="Photo of a driver's hands on a steering wheel on an open road, tinted blue"></section>
<div class="abs hero-h1">WITH A PERSONAL LOAN</div>
<div class="abs hero-h2">RATE STARTING THIS LOW,</div>
<div class="abs hero-h3">WHY WAIT ANY LONGER?</div>

<div class="abs rate-label" style="left:122px">Home Loan Rate</div>
<div class="abs rate-box" style="left:121px"><span class="num">4.69</span><span class="unit">%<br>p.a.</span></div>
<div class="abs rate-label" style="left:277px">Compare Rate</div>
<div class="abs rate-box" style="left:275px"><span class="num">4.99</span><span class="unit">%<br>p.a.</span></div>

<form class="abs quote">
  <h3>Quick Quote</h3>
  <div class="field" style="top:49px">Name *</div>
  <div class="field" style="top:82px">Purpose of Loan *<svg width="10" height="5"><path d="M0 0h10L5 5z" fill="#777"/></svg></div>
  <div class="field" style="top:116px">Loan amount *<svg width="10" height="5"><path d="M0 0h10L5 5z" fill="#777"/></svg></div>
  <div class="field" style="top:150px">Email *</div>
  <div class="btn">APPLY NOW</div>
</form>

<h2 class="abs services-title">OUR FINANCIAL SERVICES</h2>
<div class="abs tile t-vehicle" style="left:121px;top:511px" role="img" aria-label="Couple smiling in a car">VEHICLE LOAN</div>
<div class="abs tile t-boat" style="left:342px;top:511px" role="img" aria-label="Sailing boat by a rocky cliff">BOAT LOAN</div>
<div class="abs tile t-home" style="left:564px;top:511px" role="img" aria-label="White family house with garden">HOME LOAN</div>
<div class="abs tile t-personal" style="left:121px;top:658px" role="img" aria-label="Man holding a piggy bank">PERSONAL LOAN</div>
<div class="abs tile t-business" style="left:342px;top:658px" role="img" aria-label="Glass office towers against the sky">BUSINESS LOAN</div>
<div class="abs tile t-equipment" style="left:564px;top:658px" role="img" aria-label="Yellow wheel loader on a work site">EQUIPMENT LOAN</div>

<section class="abs cta">
  <h2>A <b>SMARTER</b> LOAN. YOU <b>EARNED</b> IT.</h2>
  <p>Dolor sit am consectetuer adipiscing elit, sed diam nonum nibhit euismod tincidunt ut laoreet dolore into amet.</p>
  <div class="outline">APPLY NOW</div>
</section>

<footer class="abs footer">
  <div class="abs brand"><span class="brand-mark" style="background:#3d6fc0"></span><span class="brand-name">Brightpath<br>Finance</span></div>
  <div class="abs foot-rule"></div>
  <p class="abs foot-about">Lorem ipsum dolor sit amet into ametco consectetuer intoin adipiscing elit, sedip diam nonummy nibh.</p>
  <div class="abs foot-head" style="left:512px">LOCATION</div>
  <p class="abs foot-text" style="left:512px;top:53px">Unit 12/408 Harlow Street,<br>Fenwick 2345</p>
  <div class="abs foot-head" style="left:652px">CONTACT US</div>
  <div class="abs" style="left:653px;top:50px">
    <div class="contact-row"><svg width="9" height="9" viewBox="0 0 10 10"><path d="M2 1l2 2-1 1.5c.6 1.2 1.3 1.9 2.5 2.5L7 6l2 2-1.5 1.5C4 9 1 6 .5 2.5z" fill="#777"/></svg>1300 555 014</div>
    <div class="contact-row"><svg width="9" height="9" viewBox="0 0 10 10"><rect x="1" y="3" width="8" height="6" fill="#777"/><rect x="3" y="1" width="4" height="3" fill="#777"/></svg>08 5550 2741</div>
    <div class="contact-row"><svg width="9" height="7" viewBox="0 0 10 7"><rect width="10" height="7" fill="#777"/><path d="M0 0l5 4 5-4" fill="none" stroke="#262223"/></svg>info@brightpathfinance.example.com</div>
  </div>
</footer>
<div class="abs bottom">
  <div class="abs social-foot"><span></span><span></span><span></span></div>
  <div class="abs copy">© 2016, brightpathfinance.example.com. All rights reserved.</div>
</div>

</body>
</html>
```